Maple Lantern Productions web site

I need to build a website for a new company I am launching next month. Maple Lantern Productions is a company based in New England that provides sound, lighting, and audio visual services to weddings, corporate, and any other cusomer base looking for quality service for a fair price. Looking for somebody to do a full site not just the image files. I am looking to keep the colors of my logo (orange and black) and possibly grey and white. I am looking to build my site very similar to brightvaleevents.example, which is owned by a friend of mine. I like how he has the big pictures that load in to the site and the basic menu items. I'll need a gallery of photos. The designs should communicate quality, value and trust.
My website address is maplelanternco.example.
Updates

Hi and thanks to everyone for posting such great ideas for our new design.I have some items that I'd like to ask you all to focus on in your revisions.I like how http://www.brightvaleevents.example/ website has five or six high res pictures that change in a slideshow format with a caption that loads in for each one for the different types of services. Try and capture pics like these and with teh same headings as he has. The basic menu designs have been interesting.I am more fond of the menus that are more white with some orange as I dont want it to be too dark. I'm curious to see how your galleries will work and if i'll be able to edit the pages myself? I have some more info on the company for you to fill in:website address is ciderhouseco.comemail: info@ciderhouseco.comaddress: Maple Lantern Productions57 Littlefield StreetAvon, MA 02417"New England's finest DJ's, lighting and sound, video and more. Creating memories one perfect event at a time."Put this under the loading pictures as a tagline.About Cider HouseCider House Productions is a collection of New England's finest talent, ready to make your next event the one you've dreamed of. We have the skills and expertise to deliver your vision of your perfect event. From elegant weddings to themed mitzvah's, corporate av, videography and detail lighting, we offer all of the elements to make your event a success. Added Wednesday, March 1, 2017

Designer's Please also make sure that your design flows well on any device it is being viewed on as well. Thanks. Added Wednesday, March 1, 2017

Project Deadline Extended Reason: Hello designerThank you all very much for your hard work on our project. Im sorry but i need to extend the date of my project. Our parent conpany Rook Nine Prodactions sponsors Bay Youth Assemblies and we are currently at their leadership conference on the Cape. I will be back in on Monday and with your help will get this finished by Thursday the 16th. Thanks Added Thursday, March 9, 2017

Project Deadline Extended Reason: One of the designers is not responding so I now have to make revisions with other designers. I hope to get this website done over the weekends so please get your revisions as soon as possible. Thank you. I am also upgrading the budget another $75 to hopefully get some more interest on my project. Added Wednesday, March 15, 2017

Target Market(s)

Wedding - Corporate -

Industry/Entity Type

It Company

Coding

Coded - Design and coding required

Number of Pages Required

5+ page

Font styles to use
Sans Serif

Requirements
Must have
• Photo Gallery - I want to be able to edit it myself
Nice to have
• I like the look of my friends website brightvaleevents.example

```html
<!DOCTYPE html>
<html lang="en">
<head>
<meta charset="utf-8">
<title>Maple Lantern Productions</title>
<link href="https://fonts.googleapis.com/css2?family=Open+Sans:wght@300;400;600;700&display=swap" rel="stylesheet">
<style>
:root{
  --orange:#f15a24;
  --orange-dark:#d9461a;
  --ink:#1c1c1c;
  --text:#333;
  --muted:#9a9a9a;
  --line:#dcdcdc;
  --grey:#ececec;
  --white:#fff;
  --footer:#1a1a1a;
}
*{box-sizing:border-box;margin:0;padding:0}
html,body{width:1200px;height:4401px;overflow:hidden}
body{font-family:"Open Sans",Arial,sans-serif;color:var(--text);background:var(--white);position:relative}
section,header,footer{position:relative;width:1200px}

/* header */
.site-header{height:117px;background:var(--white)}
.brand{position:absolute;left:123px;top:26px;display:flex;align-items:center;gap:14px}
.brand-dot{width:62px;height:62px;border-radius:50%;background:var(--orange)}
.brand-name{font-weight:700;color:var(--ink);font-size:25px;line-height:26px;text-transform:uppercase;letter-spacing:1px}
.phone{position:absolute;right:128px;top:16px;font-size:17px;font-weight:600;color:var(--ink);display:flex;align-items:center;gap:8px}
.main-nav{position:absolute;left:412px;top:52px;display:flex}
.main-nav a{display:block;font-size:14px;color:#555;text-decoration:none;text-transform:uppercase;padding:10px 18px;border:2px solid transparent}
.main-nav a.active{border-color:var(--orange);color:var(--ink)}

/* hero */
.hero{height:523px;overflow:hidden}
.hero-photo{position:absolute;inset:0;background:radial-gradient(ellipse at 55% 20%,#a255d8 0%,#4a2a8a 35%,#1b1640 70%,#0e0d1e 100%)}
.hero-caption{position:absolute;top:180px;width:100%;text-align:center;color:var(--white)}
.hero-kicker{font-size:38px;font-weight:400;letter-spacing:1px}
.hero-title{font-size:44px;font-weight:700;margin-top:2px}
.slider-dots{position:absolute;top:470px;left:0;width:100%;display:flex;justify-content:center;gap:10px}
.slider-dots span{width:28px;height:3px;background:rgba(255,255,255,.5)}
.slider-dots span.on{background:var(--white)}

/* welcome */
.welcome{height:410px}
.welcome-photo{position:absolute;left:159px;top:64px;width:246px;height:246px;border-radius:50%;background:radial-gradient(circle at 45% 40%,#f4a8e4,#b02aa8 50%,#4a145e)}
.welcome-body{position:absolute;left:519px;top:58px;width:540px}
.welcome h2{font-size:27px;font-weight:600;color:var(--ink);text-transform:uppercase}
.welcome h2 span{color:var(--orange)}
.small{font-size:13px;line-height:21px;color:var(--muted);margin-top:14px}
.btn-outline{position:absolute;left:6px;top:212px;width:144px;height:40px;border:2px solid #555;font-size:13px;color:#333;text-transform:uppercase;display:flex;align-items:center;justify-content:center}

/* band heading */
.band{height:118px;background:var(--orange);color:var(--white);text-align:center}
.band h2{font-size:28px;font-weight:600;line-height:118px;text-transform:uppercase}
.band::after{content:"";position:absolute;left:582px;bottom:-18px;border-left:18px solid transparent;border-right:18px solid transparent;border-top:18px solid var(--orange)}

/* services */
.services{height:1150px}
.service{position:absolute;width:1200px;height:258px}
.service-text{position:absolute;top:0;width:430px}
.service h3{font-size:32px;font-weight:300;color:var(--orange);margin-top:10px}
.service .small{margin-top:8px}
.btn-solid{display:inline-flex;align-items:center;justify-content:center;width:134px;height:40px;background:var(--orange);color:var(--white);font-size:13px;text-transform:uppercase;margin-top:14px}
.service-photo{position:absolute;top:0;width:410px;height:258px}
.divider{position:absolute;left:132px;width:930px;height:1px;background:var(--line)}

/* about */
.about{height:596px;overflow:hidden;color:var(--white)}
.about-photo{position:absolute;inset:0;background:radial-gradient(ellipse at 50% 10%,#2f4f8f 0%,#142548 40%,#0a0f1d 80%)}
.about h2{position:absolute;top:62px;width:100%;text-align:center;font-size:29px;font-weight:600;text-transform:uppercase}
.about-lead{position:absolute;left:200px;top:116px;width:800px;text-align:center;font-size:15px;line-height:24px}
.about-lead p+p{margin-top:8px}
.member{position:absolute;top:283px;width:220px;text-align:center}
.member-photo{width:130px;height:130px;margin:0 auto;border-radius:50%;border:4px solid var(--white);background:radial-gradient(circle at 50% 40%,#c9a58a,#6b5446 60%,#2e2620)}
.member h4{font-size:15px;font-weight:600;margin-top:22px;text-transform:uppercase}
.member p{font-size:12px;line-height:17px;margin-top:4px}

/* gallery */
.gallery{height:504px}
.gallery h2{position:absolute;top:45px;width:100%;text-align:center;font-size:27px;font-weight:600;color:var(--ink);text-transform:uppercase}
.gallery-grid{position:absolute;left:138px;top:111px;width:927px;display:grid;grid-template-columns:repeat(4,1fr);gap:17px 12px}
.gallery-grid div{height:156px}

/* testimonials */
.testimonials{height:396px;background:var(--orange);color:var(--white)}
.testimonials h2{position:absolute;top:44px;width:100%;text-align:center;font-size:27px;font-weight:600;text-transform:uppercase}
.testimonials::after{content:"";position:absolute;left:582px;bottom:-18px;border-left:18px solid transparent;border-right:18px solid transparent;border-top:18px solid var(--orange);z-index:2}
.quote{position:absolute;top:109px;width:400px;text-align:center}
.quote blockquote{background:var(--orange-dark);font-style:italic;font-size:13px;line-height:20px;padding:20px 28px;height:111px}
.avatar{width:62px;height:62px;margin:7px auto 0;border-radius:50%;border:3px solid var(--white);background:radial-gradient(circle at 50% 40%,#d7b49a,#7a5e4c)}
.quote cite{display:block;font-style:normal;font-weight:600;font-size:13px;margin-top:14px}

/* contact */
.contact{height:429px;background:var(--grey)}
.contact h2{position:absolute;top:78px;width:100%;text-align:center;font-size:27px;font-weight:600;color:var(--ink);text-transform:uppercase}
.field{position:absolute;background:var(--white);border:1px solid #c9c9c9;font-size:13px;color:#555;padding:12px 14px}
.btn-submit{position:absolute;left:513px;top:323px;width:142px;height:41px;background:var(--orange);color:var(--white);font-size:14px;text-transform:uppercase;display:flex;align-items:center;justify-content:center}

/* footer */
.site-footer{height:158px;background:var(--footer);color:var(--white)}
.footer-nav{position:absolute;left:106px;top:45px;display:flex;gap:34px;font-size:13px;font-weight:600;text-transform:uppercase}
.copyright{position:absolute;left:106px;top:82px;font-size:12px;color:#888}
.socials{position:absolute;left:898px;top:46px;display:flex;gap:7px}
.socials span{width:33px;height:33px;border:2px solid var(--white)}
</style>
</head>
<body>

<header class="site-header">
  <div class="brand">
    <div class="brand-dot"></div>
    <div class="brand-name">Maple Lantern<br>Productions</div>
  </div>
  <div class="phone">
    <svg width="20" height="20" viewBox="0 0 20 20"><rect width="20" height="20" rx="3" fill="#f15a24"/><path d="M6 4l2.2 2.2-1.3 1.6c.8 1.8 2.2 3.2 4 4l1.6-1.3L15 13l-1.6 2.4C9 15 5 11 4.6 6z" fill="#fff"/></svg>
    555-014-2290
  </div>
  <nav class="main-nav">
    <a class="active">Home</a><a>About Us</a><a>Services</a><a>Gallery</a><a>Team</a><a>Review</a><a>Contact</a>
  </nav>
</header>

<section class="hero">
  <div class="hero-photo" role="img" aria-label="Concert crowd under purple and blue stage lights"></div>
  <div class="hero-caption">
    <div class="hero-kicker">MAPLE LANTERN PRODUCTIONS</div>
    <div class="hero-title">SOUND, LIGHTING AND AUDIO VISUAL</div>
  </div>
  <div class="slider-dots"><span></span><span class="on"></span><span></span><span></span></div>
</section>

<section class="welcome">
  <div class="welcome-photo" role="img" aria-label="Couple sharing a first dance under pink lighting"></div>
  <div class="welcome-body">
    <h2>Welcome <span>Maple Lantern</span></h2>
    <p class="small">Our crew brings warm light, clear sound and calm planning to every room we fill, from barn weddings to ballrooms.</p>
    <p class="small">We arrive early, test every cable and stay until the last song ends, so you can enjoy the night with your guests and family.</p>
    <div class="btn-outline">Read More</div>
  </div>
</section>

<section class="band"><h2>Our Services</h2></section>

<section class="services">
  <article class="service" style="top:58px">
    <div class="service-text" style="left:138px">
      <h3>Sound &amp; Lighting</h3>
      <p class="small">Clean rigs, tuned speakers and stage lighting that follows the mood of every moment.</p>
      <p class="small">From uplights to full truss shows, we plan levels, colours and cues with you ahead of time, then run them live on the night.</p>
      <span class="btn-solid">Read More</span>
    </div>
    <div class="service-photo" style="left:631px;background:radial-gradient(circle at 50% 30%,#fff2a8,#f5a623 35%,#8a3a10 75%,#2a1206)" role="img" aria-label="Crowd with raised hands under golden stage lights"></div>
  </article>
  <div class="divider" style="top:381px"></div>
  <article class="service" style="top:425px">
    <div class="service-photo" style="left:132px;background:radial-gradient(circle at 45% 55%,#c4b0ff,#6c3bd6 35%,#2a1250 75%,#0e0820)" role="img" aria-label="DJ turntable glowing in violet light"></div>
    <div class="service-text" style="left:610px">
      <h3>Audio Visual services</h3>
      <p class="small">Projectors, screens and clear microphones for talks, awards and corporate meetings.</p>
      <p class="small">Our technicians handle slides, video playback and live feeds so each speaker looks and sounds their best in rooms of any size.</p>
      <span class="btn-solid">Read More</span>
    </div>
  </article>
  <div class="divider" style="top:748px"></div>
  <article class="service" style="top:789px">
    <div class="service-text" style="left:161px">
      <h3>Wedding &amp; Events</h3>
      <p class="small">Ceremony sound, first dance lighting and a DJ who reads the room all evening.</p>
      <p class="small">We work with your planner and venue to keep the schedule on track, from the walk down the aisle to the final sparkler exit.</p>
      <span class="btn-solid">Read More</span>
    </div>
    <div class="service-photo" style="left:651px;background:linear-gradient(135deg,#f27ad0,#c23c9e 45%,#e8e0f0 70%,#b04a9a)" role="img" aria-label="Wedding couple dancing in pink confetti light"></div>
  </article>
</section>

<section class="about">
  <div class="about-photo" role="img" aria-label="Dark stage with blue spotlights"></div>
  <h2>About Us</h2>
  <div class="about-lead">
    <p>Maple Lantern Productions is a team of skilled engineers, DJs and lighting designers ready to shape your next event.</p>
    <p>We bring the tools and the experience to deliver your vision, from elegant weddings and themed parties to corporate audio visual, video work and detail lighting across the region.</p>
  </div>
  <div class="member" style="left:151px"><div class="member-photo" role="img" aria-label="Team member portrait"></div><h4>Member Name</h4><p>Sound engineer with ten years of live stage and club work.</p></div>
  <div class="member" style="left:380px"><div class="member-photo" role="img" aria-label="Team member portrait"></div><h4>Member Name</h4><p>Event planner who keeps every schedule calm and on time.</p></div>
  <div class="member" style="left:609px"><div class="member-photo" role="img" aria-label="Team member portrait"></div><h4>Member Name</h4><p>Lighting designer who loves colour, haze and careful cues.</p></div>
  <div class="member" style="left:835px"><div class="member-photo" role="img" aria-label="Team member portrait"></div><h4>Member Name</h4><p>Video lead handling cameras, screens and live event feeds.</p></div>
</section>

<section class="gallery">
  <h2>Our Gallery</h2>
  <div class="gallery-grid">
    <div style="background:linear-gradient(160deg,#d8d4dc,#8f8a9c)" role="img" aria-label="Banquet hall with white table settings"></div>
    <div style="background:linear-gradient(160deg,#e35fc2,#6a2a8a)" role="img" aria-label="Couple dancing under pink lights"></div>
    <div style="background:linear-gradient(160deg,#e8c98a,#a06a3c)" role="img" aria-label="Reception room with warm amber lighting"></div>
    <div style="background:linear-gradient(160deg,#ecd9a8,#8c6a3e)" role="img" aria-label="Ballroom with gold draping"></div>
    <div style="background:linear-gradient(160deg,#8a5ad6,#2c1a5c)" role="img" aria-label="Dance floor lit in violet"></div>
    <div style="background:linear-gradient(160deg,#b27ad8,#4e2a86)" role="img" aria-label="Purple uplit wedding tables"></div>
    <div style="background:linear-gradient(160deg,#7c6ae0,#e0d8f4)" role="img" aria-label="Event tent lit in blue and violet"></div>
    <div style="background:linear-gradient(160deg,#9a6ad0,#3a2466)" role="img" aria-label="Reception hall with purple uplighting"></div>
  </div>
</section>

<section class="testimonials">
  <h2>Testimonials</h2>
  <div class="quote" style="left:185px">
    <blockquote>They handled every detail of our wedding and the dance floor stayed full all night long. Truly a flawless evening.</blockquote>
    <div class="avatar" role="img" aria-label="Client portrait"></div>
    <cite>By Author Name, City Location</cite>
  </div>
  <div class="quote" style="left:618px">
    <blockquote>Clear sound and sharp lighting at our annual meeting. The crew was early, friendly and easy to work with throughout.</blockquote>
    <div class="avatar" role="img" aria-label="Client portrait"></div>
    <cite>By Author Name, City Location</cite>
  </div>
</section>

<section class="contact">
  <h2>Want to Contact Us</h2>
  <div class="field" style="left:155px;top:138px;width:283px;height:45px">Your Name</div>
  <div class="field" style="left:449px;top:138px;width:283px;height:45px">Email address</div>
  <div class="field" style="left:743px;top:138px;width:284px;height:45px">Phone</div>
  <div class="field" style="left:155px;top:194px;width:872px;height:103px">Message</div>
  <div class="btn-submit">Submit</div>
</section>

<footer class="site-footer">
  <nav class="footer-nav"><span>Home</span><span>About Us</span><span>Services</span><span>Gallery</span><span>Team</span><span>Review</span><span>Contact</span></nav>
  <div class="copyright">© 2017 Company Name. All rights reserved. &nbsp; Terms of Use &nbsp;|&nbsp; Privacy Policy</div>
  <div class="socials"><span></span><span></span><span></span><span></span></div>
</footer>

</body>
</html>
```